sydney wedding photography business needs a business card design

we need a business card design for a sydney based wedding photography and videography business. our business name is :golden hour studio and film. our target clients are 24-35 yrs female. our style is candid, organic, natural, dynamic. we are a team of young photographers and videographers, and help brides to create memories that they will cherish for the rest of their lives. the logo will be provided. we want an elegant design that reflects our style, and also want to give a great impression to our clients that we are one of the best studios in sydney and our brand means quality and premium service.

Target Market(s)

bride to be, 24-35 years old, living in sydney and surrunding areas

Industry/Entity Type

Wedding Photography

Contact Information for Business Card

address: 57 tarrant street, glenmore nsw 2047
mobile: 0431872259
phone: (02) 9163 2408
info@tidewillowstudio.net.au
www.tidewillowstudio.net.au
facebook:tidewillowweddings
instagram:tidewillowweddings

Font styles to use
Serif
Sans Serif

Requirements
Nice to have
• maybe add my slogan"memories beyond eternity" if the layout looks good
Should not have
• no black color, not good idea for wedding biz card

```html
<!DOCTYPE html>
<html lang="en">
<head>
<meta charset="utf-8">
<title>Golden Hour Studio and Film – Business Card</title>
<link href="https://fonts.googleapis.com/css2?family=Marcellus&family=UnifrakturMaguntia&family=Alegreya+Sans:wght@500;700&display=swap" rel="stylesheet">
<style>
  :root {
    --page-bg: #ecebec;
    --card-bg: #3d2f2a;
    --card-glow: #54423a;
    --band-bg: #4a3a33;
    --gold: #f2c200;
    --gold-deep: #c99a00;
    --gold-text: #e9b92c;
    --cream: #f6e9bd;
  }
  * { box-sizing: border-box; margin: 0; padding: 0; }
  html, body { width: 1200px; height: 1200px; overflow: hidden; }
  body {
    background: var(--page-bg);
    display: flex;
    flex-direction: column;
    align-items: center;
    justify-content: center;
    gap: 80px;
  }
  .card {
    position: relative;
    width: 700px;
    height: 400px;
    background: var(--card-bg);
    border-radius: 44px 6px 44px 6px;
    overflow: hidden;
    box-shadow: 0 14px 30px rgba(0,0,0,.25);
  }
  .card__pattern {
    position: absolute; inset: 0;
    background: radial-gradient(ellipse at center, var(--card-glow) 0%, var(--card-bg) 75%);
  }
  .gold-rule {
    position: absolute; left: 0; right: 0;
    height: 3px;
    background: var(--gold);
  }
  .gold-rule--top { top: 42px; }
  .gold-rule--bottom { bottom: 42px; }
  .gold-rule__bar {
    position: absolute; top: -3px;
    width: 280px; height: 9px;
    background: linear-gradient(to bottom, var(--gold), var(--gold-deep));
    border-radius: 2px;
  }
  .gold-rule--top .gold-rule__bar { left: 180px; }
  .gold-rule--bottom .gold-rule__bar { right: 180px; }

  .brand {
    position: absolute; inset: 0;
    display: flex; align-items: center; justify-content: center;
    gap: 16px;
  }
  .brand__mark {
    width: 14px; height: 14px; border-radius: 50%;
    background: var(--gold-text);
  }
  .brand__name {
    font-family: "Marcellus", serif;
    font-size: 40px;
    color: var(--gold-text);
    letter-spacing: 1px;
  }

  .contact {
    position: absolute; left: 0; right: 0; top: 84px;
    text-align: center;
    color: var(--cream);
  }
  .contact__name {
    font-family: "UnifrakturMaguntia", serif;
    font-size: 42px;
    line-height: 1;
  }
  .contact__role {
    font-family: "Marcellus", serif;
    font-size: 19px;
    letter-spacing: 1px;
    margin-top: 4px;
  }
  .contact__phone {
    font-family: "Alegreya Sans", sans-serif;
    font-weight: 700;
    font-size: 21px;
    letter-spacing: 1.5px;
    margin-top: 20px;
  }
  .contact__web {
    font-family: "Alegreya Sans", sans-serif;
    font-weight: 500;
    font-size: 20px;
    letter-spacing: 1px;
    margin-top: 8px;
  }
  .card__band {
    position: absolute; left: 0; right: 0;
    top: 290px; height: 54px;
    background: var(--band-bg);
    display: flex; align-items: center; justify-content: center;
    font-family: "Marcellus", serif;
    font-size: 20px;
    letter-spacing: 1.5px;
    color: var(--cream);
  }
  .card--back .gold-rule--bottom { bottom: 34px; }
</style>
</head>
<body>

  <section class="card card--front">
    <div class="card__pattern" role="img" aria-label="Subtle warm floral damask pattern"></div>
    <div class="gold-rule gold-rule--top"><span class="gold-rule__bar"></span></div>
    <div class="gold-rule gold-rule--bottom"><span class="gold-rule__bar"></span></div>
    <div class="brand">
      <span class="brand__mark"></span>
      <span class="brand__name">golden hour studio and film</span>
    </div>
  </section>

  <section class="card card--back">
    <div class="card__pattern" role="img" aria-label="Subtle warm floral damask pattern"></div>
    <div class="gold-rule gold-rule--top"><span class="gold-rule__bar"></span></div>
    <div class="contact">
      <p class="contact__name">John Doe</p>
      <p class="contact__role">Director</p>
      <p class="contact__phone">0431872259 | (02) 9163 2408</p>
      <p class="contact__web">www.tidewillowstudio.net.au | info@tidewillowstudio.net.au</p>
    </div>
    <div class="card__band">57 tarrant street, glenmore nsw 2047</div>
    <div class="gold-rule gold-rule--bottom"><span class="gold-rule__bar"></span></div>
  </section>

</body>
</html>
```